Business Card for a Dental Office

The design should communicate integrity, quality and reliability. We also want the card look elegant, simple, but still stand out, different from the traditional-dental-office business card.

Industry/Entity Type

Business

```html
<!DOCTYPE html>
<html lang="en">
<head>
<meta charset="utf-8">
<title>Larkfield Dental Studio – Business Card</title>
<link rel="stylesheet" href="https://fonts.googleapis.com/css2?family=Oswald:wght@600&family=Open+Sans:wght@400;700&display=swap">
<style>
  :root {
    --backdrop: #d9d9d7;
    --ink: #0b0b0b;
    --paper: #ffffff;
    --gold: #c9a227;
    --yellow-light: #f3e51c;
    --yellow-deep: #c8b02c;
    --shadow: rgba(0, 0, 0, 0.28);
  }
  html, body {
    margin: 0;
    width: 1200px;
    height: 900px;
    overflow: hidden;
    background: var(--backdrop);
  }
  .canvas {
    position: relative;
    width: 1200px;
    height: 900px;
  }
  .card {
    position: absolute;
    left: 320px;
    width: 560px;
    height: 320px;
    overflow: hidden;
    box-shadow: 0 10px 26px var(--shadow);
  }
  .card--front { top: 100px; background: var(--ink); }
  .card--back  { top: 480px; background: var(--yellow-light); }

  /* Front */
  .brand {
    position: absolute;
    left: 0; right: 0; top: 118px;
    display: flex;
    flex-direction: column;
    align-items: center;
  }
  .brand__row {
    display: flex;
    align-items: center;
    gap: 14px;
  }
  .brand__square {
    width: 34px; height: 34px;
    background: var(--gold);
  }
  .brand__name {
    font-family: "Oswald", sans-serif;
    font-weight: 600;
    font-size: 34px;
    letter-spacing: 0.5px;
    color: var(--paper);
    line-height: 1;
  }
  .brand__tagline {
    margin-top: 10px;
    font-family: "Open Sans", sans-serif;
    font-weight: 700;
    font-size: 13px;
    letter-spacing: 1.6px;
    color: var(--gold);
    text-transform: uppercase;
  }

  /* Back */
  .back__shape { position: absolute; inset: 0; }
  .back__brand {
    position: absolute;
    left: 34px; top: 128px;
    display: flex;
    align-items: center;
    gap: 10px;
  }
  .back__brand .brand__square { width: 26px; height: 26px; }
  .back__brand .brand__name { font-size: 22px; line-height: 1.1; }
  .contact {
    position: absolute;
    right: 28px; top: 40px;
    text-align: right;
    font-family: "Open Sans", sans-serif;
    color: var(--ink);
  }
  .contact__name { font-weight: 700; font-size: 17px; margin: 0; }
  .contact__title { font-size: 14px; margin: 0 0 20px; }
  .contact__list { list-style: none; margin: 0; padding: 0; }
  .contact__item {
    display: flex;
    justify-content: flex-end;
    align-items: center;
    gap: 8px;
    font-size: 15px;
    line-height: 22px;
  }
  .contact__item--gap { margin-top: 8px; }
  .icon { width: 12px; height: 12px; fill: var(--ink); flex: none; }
</style>
</head>
<body>
<main class="canvas">

  <section class="card card--front" aria-label="Card front">
    <div class="brand">
      <div class="brand__row">
        <span class="brand__square"></span>
        <span class="brand__name">LARKFIELD DENTAL STUDIO</span>
      </div>
      <div class="brand__tagline">Your smile is your gift to others</div>
    </div>
  </section>

  <section class="card card--back" aria-label="Card back">
    <svg class="back__shape" viewBox="0 0 560 320" width="560" height="320" aria-hidden="true">
      <defs>
        <linearGradient id="yellowFill" x1="0" y1="0" x2="0" y2="1">
          <stop offset="0" stop-color="#f3e51c"/>
          <stop offset="1" stop-color="#c8b02c"/>
        </linearGradient>
      </defs>
      <rect width="560" height="320" fill="url(#yellowFill)"/>
      <path d="M0 0 H282 C400 70 405 240 232 320 H0 Z" fill="#ffffff"/>
      <path d="M0 0 H262 C372 70 380 235 205 320 H0 Z" fill="#0b0b0b"/>
    </svg>

    <div class="back__brand">
      <span class="brand__square"></span>
      <span class="brand__name">LARKFIELD<br>DENTAL STUDIO</span>
    </div>

    <div class="contact">
      <p class="contact__name">Daniel Harper</p>
      <p class="contact__title">Managing Director</p>
      <ul class="contact__list">
        <li class="contact__item">123.456.7890
          <svg class="icon" viewBox="0 0 12 12"><path d="M2 1h2l1 3-1.5 1a7 7 0 0 0 3.5 3.5L8 7l3 1v2a1 1 0 0 1-1 1A9 9 0 0 1 1 2a1 1 0 0 1 1-1z"/></svg>
        </li>
        <li class="contact__item">123.456.7890
          <svg class="icon" viewBox="0 0 12 12"><rect x="3" y="0.5" width="6" height="11" rx="1"/><rect x="4" y="2" width="4" height="6" fill="#e6d420"/></svg>
        </li>
        <li class="contact__item">info@youremail.com
          <svg class="icon" viewBox="0 0 12 12"><rect x="0.5" y="2" width="11" height="8"/><path d="M1 2.5 6 6.5 11 2.5" stroke="#e6d420" stroke-width="1" fill="none"/></svg>
        </li>
        <li class="contact__item">www.website.com
          <svg class="icon" viewBox="0 0 12 12"><path d="M5 7 7 5M4.5 5.5 3 7a1.8 1.8 0 0 0 2.5 2.5L7 8M7.5 6.5 9 5a1.8 1.8 0 0 0-2.5-2.5L5 4" stroke="#0b0b0b" stroke-width="1.3" fill="none"/></svg>
        </li>
        <li class="contact__item contact__item--gap">1234, Address Goes Here
          <svg class="icon" viewBox="0 0 12 12"><path d="M6 0.5a4 4 0 0 1 4 4C10 7.5 6 11.5 6 11.5S2 7.5 2 4.5a4 4 0 0 1 4-4z"/><circle cx="6" cy="4.5" r="1.4" fill="#d9c726"/></svg>
        </li>
        <li class="contact__item">Country Name, 123456</li>
      </ul>
    </div>
  </section>

</main>
</body>
</html>
```